High-end construction company needs a business card design

We need a modern looking business card that draws people in, is memorable and looks so good people will want to sick it on their fridges.
On the first side what is needed are:
Logo
My name - Tomasz Brelwik
Title - Managing Director
Website - www.varkelt.co.uk
Email - tomasz@varkelt.co.uk
Telephone - 020 5194 6281
Mobile - 07845139072
On the back side was is needed is a list of all the services we provide:
-Kitchen Renovations
-Bathroom Renovations
-House Renovations
-Garage Conversions
-Extensions
-Loft Conversions
-Conservatories
-Carpentry
-Tiling
-Electrical
-Plumbing & Heating
-Bricklaying
-Landscaping
-Decorating
-Plastering
We would like the colours to be the same shades as on the logo with grey or black for the words.
Target Market(s)
Anyone who needs building work done
Contact Information for Business Card
This business card is for a construction company which strives to deliver excellent service and quality.
The look and feel of the card should represent this.
Requirements
Must have
- On the first side what is needed are:
Logo
My name - Tomasz Brelwik
Title - Managing Director
Website - www.varkelt.co.uk
Email - tomasz@varkelt.co.uk
Telephone - 020 5194 6281
Mobile - 07845139072
Nice to have
- Cool looking features

```html
<!DOCTYPE html>
<html lang="en">
<head>
<meta charset="utf-8">
<title>Varkelt Construction Ltd – Business Card</title>
<link rel="stylesheet" href="https://fonts.googleapis.com/css2?family=Arimo:wght@400;700&display=swap">
<style>
  :root {
    --page-bg: #e4e1e1;
    --card-frost: #efeaea;
    --green-light: #72bd44;
    --green-dark: #479140;
    --green-faint: rgba(114, 189, 68, 0.22);
    --text-on-green: #ffffff;
  }
  * { box-sizing: border-box; margin: 0; padding: 0; }
  html, body {
    width: 1200px;
    height: 1181px;
    overflow: hidden;
    background: var(--page-bg);
    font-family: "Arimo", Arial, sans-serif;
  }
  .canvas { position: relative; width: 1200px; height: 1181px; }

  .card {
    position: absolute;
    width: 654px;
    height: 404px;
    background: var(--card-frost);
    overflow: visible;
  }
  .card--front { left: 181px; top: 156px; }
  .card--back  { left: 480px; top: 627px; }

  /* Front */
  .front-panel {
    position: absolute;
    left: 0; top: 0;
    width: 320px; height: 404px;
    background: var(--green-light);
  }
  .front-notch {
    position: absolute;
    left: 283px; top: 154px;
    width: 37px; height: 67px;
  }
  .holder { position: absolute; left: 38px; top: 44px; color: var(--text-on-green); }
  .holder__name { font-weight: 700; font-size: 26px; line-height: 1; letter-spacing: 0.2px; }
  .holder__title { font-size: 19px; line-height: 1; margin-top: 3px; }

  .contacts { position: absolute; left: 38px; top: 266px; list-style: none; color: var(--text-on-green); }
  .contacts li {
    display: flex; align-items: center;
    height: 23.7px;
    font-size: 19.5px;
  }
  .contacts svg { width: 18px; height: 18px; margin-right: 8px; flex: none; }

  .brand {
    position: absolute;
    left: 368px; top: 150px;
    width: 258px;
    text-align: center;
    color: var(--green-dark);
    font-weight: 700;
  }
  .brand__name { font-size: 58px; line-height: 1; letter-spacing: 1px; }
  .brand__sub { font-size: 16px; letter-spacing: 3.4px; margin-top: 8px; }

  /* Back */
  .back-panel {
    position: absolute;
    left: 324px; top: 0;
    width: 330px; height: 404px;
    background: var(--green-dark);
  }
  .back-point {
    position: absolute;
    left: 324px; top: 154px;
    width: 37px; height: 67px;
  }
  .brand--faint { left: 38px; top: 215px; color: var(--green-faint); }

  .services {
    position: absolute;
    right: 50px; top: 29px;
    list-style: none;
    text-align: right;
    color: var(--text-on-green);
  }
  .services li {
    position: relative;
    height: 22.8px;
    font-size: 19.5px;
    line-height: 22.8px;
  }
  .services li::after {
    content: "";
    position: absolute;
    right: -15px; top: 8px;
    width: 9px; height: 9px;
    border-radius: 50%;
    background: var(--green-light);
  }
</style>
</head>
<body>
<main class="canvas">

  <section class="card card--front" aria-label="Business card front">
    <div class="front-panel"></div>
    <svg class="front-notch" viewBox="0 0 37 67" aria-hidden="true">
      <polygon points="37,0 37,67 0,30" fill="var(--card-frost)"/>
      <g fill="var(--green-light)">
        <rect x="18" y="25" width="4" height="4"/><rect x="23" y="25" width="4" height="4"/>
        <rect x="18" y="30" width="4" height="4"/><rect x="23" y="30" width="4" height="4"/>
      </g>
    </svg>

    <div class="holder">
      <p class="holder__name">TOMASZ BRELWIK</p>
      <p class="holder__title">Managing Director</p>
    </div>

    <ul class="contacts">
      <li>
        <svg viewBox="0 0 24 24" fill="none" stroke="#fff" stroke-width="2" stroke-linejoin="round"><path d="M5 3h4l2 5-3 2a12 12 0 0 0 6 6l2-3 5 2v4a2 2 0 0 1-2 2A17 17 0 0 1 3 5a2 2 0 0 1 2-2z"/></svg>
        020 5194 6281
      </li>
      <li>
        <svg viewBox="0 0 24 24" fill="none" stroke="#fff" stroke-width="2"><rect x="6" y="2" width="12" height="20" rx="2"/><line x1="10" y1="18" x2="14" y2="18"/></svg>
        07845139072
      </li>
      <li>
        <svg viewBox="0 0 24 24" fill="none" stroke="#fff" stroke-width="2"><rect x="2" y="5" width="20" height="14"/><polyline points="2,5 12,13 22,5"/></svg>
        tomasz@varkelt.co.uk
      </li>
      <li>
        <svg viewBox="0 0 24 24" fill="none" stroke="#fff" stroke-width="1.8"><circle cx="12" cy="12" r="10"/><ellipse cx="12" cy="12" rx="4.5" ry="10"/><line x1="2" y1="12" x2="22" y2="12"/><line x1="4" y1="7" x2="20" y2="7"/><line x1="4" y1="17" x2="20" y2="17"/></svg>
        www.varkelt.co.uk
      </li>
    </ul>

    <div class="brand">
      <p class="brand__name">VARKELT</p>
      <p class="brand__sub">CONSTRUCTION LTD</p>
    </div>
  </section>

  <section class="card card--back" aria-label="Business card back">
    <div class="back-panel"></div>
    <svg class="back-point" viewBox="0 0 37 67" aria-hidden="true">
      <polygon points="0,0 37,30 0,67" fill="var(--green-dark)"/>
      <g fill="var(--text-on-green)">
        <rect x="2" y="25" width="4" height="4"/><rect x="7" y="25" width="4" height="4"/>
        <rect x="2" y="30" width="4" height="4"/><rect x="7" y="30" width="4" height="4"/>
      </g>
    </svg>

    <div class="brand brand--faint">
      <p class="brand__name">VARKELT</p>
      <p class="brand__sub">CONSTRUCTION LTD</p>
    </div>

    <ul class="services">
      <li>Kitchen Renovations</li>
      <li>Bathroom Renovations</li>
      <li>House Renovations</li>
      <li>Garage Conversions</li>
      <li>Extensions</li>
      <li>Loft Conversions</li>
      <li>Conservatories</li>
      <li>Carpentry</li>
      <li>Tiling</li>
      <li>Electrical</li>
      <li>Plumbing &amp; Heating</li>
      <li>Bricklaying</li>
      <li>Landscaping</li>
      <li>Decorating</li>
      <li>Plastering</li>
    </ul>
  </section>

</main>
</body>
</html>
```